I would like to modify/update my 2 step login screen

I want a more modern looking login page for our document imaging application. I need to keep all of the same elements and buttons that currently exist. The first 2 screens are the login. The 3rd is a screenshot of the actual application home page.

```html
<!DOCTYPE html>
<html lang="en">
<head>
<meta charset="utf-8">
<title>Meridian Docs – Login States</title>
<link rel="stylesheet" href="https://fonts.googleapis.com/css2?family=Inter:wght@400;500;600;700&display=swap">
<style>
:root{
  --page:#f0f0f0;
  --panel-dark:#050505;
  --white:#ffffff;
  --ink:#1c1c1c;
  --muted:#8a8a8a;
  --faint:#b9b9b9;
  --rule:#dcdcdc;
  --green:#5cb85c;
  --green-dark:#4caa4c;
  --blue:#4a7fd4;
  --red:#e05252;
  --disabled:#c9c9c9;
  --link:#3a6fd0;
}
*{box-sizing:border-box;margin:0;padding:0}
html,body{width:1200px;height:482px;overflow:hidden;background:var(--page);font-family:"Inter",Arial,sans-serif;color:var(--ink)}
.stage{position:absolute;left:0;top:0;width:2576px;height:1036px;transform:scale(.46584);transform-origin:0 0}
.card{position:absolute;width:796px;height:447px;background:var(--white);overflow:hidden}
.col1{left:47px}.col2{left:890px}.col3{left:1733px}
.row1{top:47px}.row2{top:541px}

/* showcase panel */
.showcase{position:absolute;left:0;top:0;width:349px;height:447px;background:var(--panel-dark);color:var(--white);text-align:center}
.showcase-art{position:absolute;left:55px;top:85px;width:240px;height:160px;border-radius:6px;
  background:radial-gradient(ellipse at 50% 40%,#3b4a3d 0%,#1a1f1b 55%,#050505 100%)}
.showcase-title{position:absolute;left:0;right:0;top:264px;font-size:14.5px;font-weight:700}
.showcase-text{position:absolute;left:60px;right:60px;top:289px;font-size:8px;line-height:12.5px;color:#e6e6e6}
.dots{position:absolute;left:0;right:0;top:336px;display:flex;justify-content:center;gap:6px}
.dots span{width:5px;height:5px;border-radius:50%;background:#555}
.dots span:first-child{background:var(--green)}

/* form panel */
.form{position:absolute;left:455px;top:0;width:234px;height:447px}
.brand{position:absolute;left:0;right:0;top:42px;display:flex;justify-content:center;align-items:center;gap:7px}
.brand-mark{width:20px;height:20px;background:var(--ink)}
.brand-name{font-size:13px;font-weight:700;letter-spacing:.5px;color:var(--ink)}
.tabs{position:absolute;left:0;width:234px;display:flex;border-bottom:1px solid #e6e6e6}
.tab{flex:1;text-align:center;font-size:12px;font-weight:600;color:var(--faint);padding-bottom:7px}
.tab.active{color:var(--ink);box-shadow:inset 0 -2px 0 var(--green)}
.field{position:absolute;left:0;width:234px;border-bottom:1px solid #e3e3e3}
.field .placeholder{font-size:9px;color:var(--muted);padding-bottom:5px}
.field .label{font-size:6.5px;color:var(--muted);margin-bottom:4px}
.field .value{font-size:9.5px;color:var(--ink);padding-bottom:6px}
.field .dots-pw{font-size:12px;letter-spacing:.5px;line-height:10px;padding-bottom:5px}
.field.focus{border-bottom:1.5px solid var(--blue)}
.field.error{border-bottom:1.5px solid var(--red)}
.field.error .label{color:var(--red)}
.eye{position:absolute;right:0;bottom:5px;width:10px;height:10px}
.option{position:absolute;left:0;width:234px;display:flex;align-items:center;font-size:7.5px;color:#333}
.check{width:11px;height:11px;border:1px solid #bdbdbd;border-radius:2px;margin-right:7px;display:flex;align-items:center;justify-content:center}
.check.on{background:var(--green);border-color:var(--green)}
.forgot{margin-left:auto;color:var(--link)}
.btn{position:absolute;left:0;width:234px;height:28px;border-radius:2px;display:flex;align-items:center;justify-content:center;font-size:8px;font-weight:600;letter-spacing:.3px;color:var(--white)}
.btn.off{background:var(--disabled);color:#eeeeee}
.btn.on{background:var(--green)}
.notice{position:absolute;left:0;right:0;text-align:center;font-size:6.5px;line-height:10px;color:#444}
.notice b{font-weight:700;color:var(--ink)}
.social{position:absolute;left:0;right:0;display:flex;justify-content:center;align-items:center;gap:12px;font-size:7.5px;color:#333}
.social .chip{width:13px;height:13px;border-radius:50%;background:#cfcfcf}
.social .chip.dark{background:var(--ink)}
.footer{position:absolute;left:0;right:0;top:409px;text-align:center;font-size:6.5px;color:#333}
.footer span+span::before{content:"•";margin:0 6px;color:var(--faint)}
.copyright{position:absolute;left:0;right:0;top:425px;text-align:center;font-size:6.5px;color:var(--muted)}
.toast{position:absolute;left:446px;top:0;width:226px;height:21px;background:var(--red);color:var(--white);font-size:7.5px;display:flex;align-items:center;padding-left:8px}
.toast .sep{margin-left:auto;width:1px;height:10px;background:rgba(255,255,255,.6)}
.toast svg{margin:0 7px 0 7px}
</style>
</head>
<body>
<div class="stage">

<!-- Row 1: database login states -->
<section class="card col1 row1">
  <div class="showcase"><div class="showcase-art" role="img" aria-label="Application dashboard shown on a laptop with green accent shapes"></div><h2 class="showcase-title">Intutive Dashboard</h2><p class="showcase-text">Temporibus autem quibusdam et aut officiis debitis aut rerum necessitatibus saepe eveniet ut et voluptates</p><div class="dots"><span></span><span></span><span></span></div></div>
  <div class="form">
    <div class="brand"><span class="brand-mark"></span><span class="brand-name">MERIDIAN DOCS</span></div>
    <div class="tabs" style="top:98px"><div class="tab active">MDS Login</div><div class="tab">Classic Login</div></div>
    <div class="field" style="top:151px"><div class="placeholder">Database</div></div>
    <div class="option" style="top:181px"><span class="check"></span>Remember Me</div>
    <div class="btn off" style="top:220px">LOGIN</div>
    <p class="notice" style="top:262px">All activity on this site is being recorded.<br>Your IP Address is being saved as '<b>192.168.168.134</b>'.</p>
    <div class="social" style="top:312px">Or Login With:<span class="chip"></span><span class="chip dark"></span><span class="chip"></span></div>
    <p class="footer"><span>Privacy</span><span>Remote Support</span><span>Contact Us</span></p>
    <p class="copyright">Copyright 2007-2024 Meridian Docs Group</p>
  </div>
</section>

<section class="card col2 row1">
  <div class="showcase"><div class="showcase-art" role="img" aria-label="Application dashboard shown on a laptop with green accent shapes"></div><h2 class="showcase-title">Intutive Dashboard</h2><p class="showcase-text">Temporibus autem quibusdam et aut officiis debitis aut rerum necessitatibus saepe eveniet ut et voluptates</p><div class="dots"><span></span><span></span><span></span></div></div>
  <div class="form">
    <div class="brand"><span class="brand-mark"></span><span class="brand-name">MERIDIAN DOCS</span></div>
    <div class="tabs" style="top:98px"><div class="tab active">MDS Login</div><div class="tab">Classic Login</div></div>
    <div class="field focus" style="top:151px"><div class="label">Database</div><div class="value">ABC12345|</div></div>
    <div class="option" style="top:192px"><span class="check on"><svg width="7" height="6" viewBox="0 0 7 6"><path d="M1 3l2 2 3-4" fill="none" stroke="#fff" stroke-width="1.3"/></svg></span>Remember Me</div>
    <div class="btn on" style="top:232px">LOGIN</div>
    <p class="notice" style="top:274px">All activity on this site is being recorded.<br>Your IP Address is being saved as '<b>192.168.168.134</b>'.</p>
    <div class="social" style="top:324px">Or Login With:<span class="chip"></span><span class="chip dark"></span><span class="chip"></span></div>
    <p class="footer"><span>Privacy</span><span>Remote Support</span><span>Contact Us</span></p>
    <p class="copyright">Copyright 2007-2024 Meridian Docs Group</p>
  </div>
</section>

<section class="card col3 row1">
  <div class="showcase"><div class="showcase-art" role="img" aria-label="Application dashboard shown on a laptop with green accent shapes"></div><h2 class="showcase-title">Intutive Dashboard</h2><p class="showcase-text">Temporibus autem quibusdam et aut officiis debitis aut rerum necessitatibus saepe eveniet ut et voluptates</p><div class="dots"><span></span><span></span><span></span></div></div>
  <div class="toast">Login failed! Please enter correct entries.<span class="sep"></span><svg width="8" height="8" viewBox="0 0 8 8"><path d="M1 1l6 6M7 1L1 7" stroke="#fff" stroke-width="1.2"/></svg></div>
  <div class="form">
    <div class="brand"><span class="brand-mark"></span><span class="brand-name">MERIDIAN DOCS</span></div>
    <div class="tabs" style="top:98px"><div class="tab active">MDS Login</div><div class="tab">Classic Login</div></div>
    <div class="field error" style="top:151px"><div class="label">Database</div><div class="value">ABC12345XYZ</div></div>
    <div class="option" style="top:192px"><span class="check on"><svg width="7" height="6" viewBox="0 0 7 6"><path d="M1 3l2 2 3-4" fill="none" stroke="#fff" stroke-width="1.3"/></svg></span>Remember Me</div>
    <div class="btn on" style="top:232px">LOGIN</div>
    <p class="notice" style="top:274px">All activity on this site is being recorded.<br>Your IP Address is being saved as '<b>192.168.168.134</b>'.</p>
    <div class="social" style="top:324px">Or Login With:<span class="chip"></span><span class="chip dark"></span><span class="chip"></span></div>
    <p class="footer"><span>Privacy</span><span>Remote Support</span><span>Contact Us</span></p>
    <p class="copyright">Copyright 2007-2024 Meridian Docs Group</p>
  </div>
</section>

<!-- Row 2: classic login states -->
<section class="card col1 row2">
  <div class="showcase"><div class="showcase-art" role="img" aria-label="Application dashboard shown on a laptop with green accent shapes"></div><h2 class="showcase-title">Intutive Dashboard</h2><p class="showcase-text">Temporibus autem quibusdam et aut officiis debitis aut rerum necessitatibus saepe eveniet ut et voluptates</p><div class="dots"><span></span><span></span><span></span></div></div>
  <div class="form">
    <div class="brand"><span class="brand-mark"></span><span class="brand-name">MERIDIAN DOCS</span></div>
    <div class="tabs" style="top:98px"><div class="tab">MDS Login</div><div class="tab active">Classic Login</div></div>
    <div class="field" style="top:152px"><div class="placeholder">Username</div></div>
    <div class="field" style="top:183px"><div class="placeholder">Password</div><svg class="eye" viewBox="0 0 10 10"><path d="M1 5c2-3 6-3 8 0-2 3-6 3-8 0z" fill="none" stroke="#999" stroke-width=".8"/><circle cx="5" cy="5" r="1.3" fill="#999"/><path d="M2 8.5L8 1.5" stroke="#999" stroke-width=".8"/></svg></div>
    <div class="option" style="top:213px"><span class="check"></span>Remember Me<span class="forgot">Forgot Password?</span></div>
    <div class="btn off" style="top:252px">LOGIN</div>
    <div class="social" style="top:309px">Or Login With:<span class="chip"></span><span class="chip dark"></span><span class="chip"></span></div>
    <p class="footer"><span>Privacy</span><span>Remote Support</span><span>Contact Us</span></p>
    <p class="copyright">Copyright 2007-2024 Meridian Docs Group</p>
  </div>
</section>

<section class="card col2 row2">
  <div class="showcase"><div class="showcase-art" role="img" aria-label="Application dashboard shown on a laptop with green accent shapes"></div><h2 class="showcase-title">Intutive Dashboard</h2><p class="showcase-text">Temporibus autem quibusdam et aut officiis debitis aut rerum necessitatibus saepe eveniet ut et voluptates</p><div class="dots"><span></span><span></span><span></span></div></div>
  <div class="form">
    <div class="brand"><span class="brand-mark"></span><span class="brand-name">MERIDIAN DOCS</span></div>
    <div class="tabs" style="top:98px"><div class="tab">MDS Login</div><div class="tab active">Classic Login</div></div>
    <div class="field" style="top:151px"><div class="label">Username</div><div class="value">jane.roe@example.com</div></div>
    <div class="field focus" style="top:193px"><div class="label">Password</div><div class="value dots-pw">●●●●●●●●●|</div><svg class="eye" viewBox="0 0 10 10"><path d="M1 5c2-3 6-3 8 0-2 3-6 3-8 0z" fill="none" stroke="#999" stroke-width=".8"/><circle cx="5" cy="5" r="1.3" fill="#999"/><path d="M2 8.5L8 1.5" stroke="#999" stroke-width=".8"/></svg></div>
    <div class="option" style="top:235px"><span class="check on"><svg width="7" height="6" viewBox="0 0 7 6"><path d="M1 3l2 2 3-4" fill="none" stroke="#fff" stroke-width="1.3"/></svg></span>Remember Me<span class="forgot">Forgot Password?</span></div>
    <div class="btn on" style="top:274px">LOGIN</div>
    <div class="social" style="top:331px">Or Login With:<span class="chip"></span><span class="chip dark"></span><span class="chip"></span></div>
    <p class="footer"><span>Privacy</span><span>Remote Support</span><span>Contact Us</span></p>
    <p class="copyright">Copyright 2007-2024 Meridian Docs Group</p>
  </div>
</section>

<section class="card col3 row2">
  <div class="showcase"><div class="showcase-art" role="img" aria-label="Application dashboard shown on a laptop with green accent shapes"></div><h2 class="showcase-title">Intutive Dashboard</h2><p class="showcase-text">Temporibus autem quibusdam et aut officiis debitis aut rerum necessitatibus saepe eveniet ut et voluptates</p><div class="dots"><span></span><span></span><span></span></div></div>
  <div class="toast">Login failed! Please enter correct entries.<span class="sep"></span><svg width="8" height="8" viewBox="0 0 8 8"><path d="M1 1l6 6M7 1L1 7" stroke="#fff" stroke-width="1.2"/></svg></div>
  <div class="form">
    <div class="brand"><span class="brand-mark"></span><span class="brand-name">MERIDIAN DOCS</span></div>
    <div class="tabs" style="top:98px"><div class="tab">MDS Login</div><div class="tab active">Classic Login</div></div>
    <div class="field error" style="top:151px"><div class="label">Username</div><div class="value">jane.roe@example.com</div></div>
    <div class="field error" style="top:193px"><div class="label">Password</div><div class="value dots-pw">●●●●●●●●●</div><svg class="eye" viewBox="0 0 10 10"><path d="M1 5c2-3 6-3 8 0-2 3-6 3-8 0z" fill="none" stroke="#999" stroke-width=".8"/><circle cx="5" cy="5" r="1.3" fill="#999"/><path d="M2 8.5L8 1.5" stroke="#999" stroke-width=".8"/></svg></div>
    <div class="option" style="top:235px"><span class="check on"><svg width="7" height="6" viewBox="0 0 7 6"><path d="M1 3l2 2 3-4" fill="none" stroke="#fff" stroke-width="1.3"/></svg></span>Remember Me<span class="forgot">Forgot Password?</span></div>
    <div class="btn on" style="top:274px">LOGIN</div>
    <div class="social" style="top:331px">Or Login With:<span class="chip"></span><span class="chip dark"></span><span class="chip"></span></div>
    <p class="footer"><span>Privacy</span><span>Remote Support</span><span>Contact Us</span></p>
    <p class="copyright">Copyright 2007-2024 Meridian Docs Group</p>
  </div>
</section>

</div>
</body>
</html>
```